a business advisory consulting website

I need a website 3-5 pages to sell my professional services in IT and Project management Consulting. My company name is Crestline Advisory Consulting. I want it to be device friendly and easy to navigate for the busy executive however intriguing enough.
I have attached some info I drafted on About the company and personal Bio. Also there is a website that I really like that I have attached the initial site pdf and websites that I like are here: https://tollmeradvisors.example, https://quarvelanalytics.example, https://www.dorvikstudylearning.example as examples. Thanks
Updates

Hi Designers, I have uploaded the logo in 3D .png format, to assist in the web design.

Target Market(s)

B2B, governments, IT companies, Project Management companies and Consulting firms, small medium enterprises to large corporate enterprises.

Industry/Entity Type

It Professional

Coding

Coded - Design and coding required

Number of Pages Required

5+ page

Font styles to use
Sans Serif

Requirements
Must have
• Home, About company, the team, what we do and contact us
Nice to have
• Blog
Should not have
• pop ups, flash

```html
<!DOCTYPE html>
<html lang="en">
<head>
<meta charset="utf-8">
<title>Crestline Advisory Consulting</title>
<link href="https://fonts.googleapis.com/css2?family=Roboto:wght@300;400;500;700&family=Open+Sans:wght@400;600;700&display=swap" rel="stylesheet">
<style>
:root{
  --navy:#121a33;
  --navy-deep:#0b1226;
  --red:#e3232f;
  --ink:#2a2f3d;
  --muted:#8a8f9c;
  --pale:#f2f3f8;
  --white:#ffffff;
  --line:#d8dbe4;
}
*{box-sizing:border-box;margin:0;padding:0}
html,body{width:1200px;height:3556px;overflow:hidden}
body{position:relative;background:var(--white);font-family:"Open Sans",sans-serif;color:var(--ink)}
.abs{position:absolute}
.heading{font-family:"Roboto",sans-serif;font-weight:300;text-transform:uppercase;letter-spacing:2px}
.red{color:var(--red)}
.btn{position:absolute;display:flex;align-items:center;gap:8px;background:var(--red);color:var(--white);font:700 11px "Open Sans",sans-serif;text-transform:uppercase;border-radius:22px;padding:0 20px;height:40px;letter-spacing:.5px}
.btn svg{width:14px;height:14px}
.btn-dot{width:18px;height:18px;border-radius:50%;background:var(--white);display:inline-block}

/* header */
.site-header{position:absolute;left:0;top:0;width:1200px;height:72px;background:var(--white);z-index:3}
.brand{position:absolute;left:110px;top:20px;display:flex;align-items:center;gap:10px;font:700 20px "Roboto",sans-serif;color:var(--navy);text-transform:uppercase}
.brand-mark{width:28px;height:28px;border-radius:50%;background:var(--red)}
.main-nav{position:absolute;left:470px;top:28px;display:flex;gap:30px;font:600 12px "Open Sans",sans-serif;color:var(--navy);text-transform:uppercase}
.main-nav span:first-child{color:var(--red)}
.search{position:absolute;left:1040px;top:26px}

/* hero */
.hero{position:absolute;left:0;top:72px;width:1200px;height:600px}
.hero-title{left:145px;top:140px;color:var(--white);font-size:72px;line-height:88px}
.hero-sub{left:145px;top:350px;color:var(--white);font:700 23px/36px "Open Sans",sans-serif}
.slider-dots{left:1126px;top:375px;display:flex;flex-direction:column;gap:10px}
.slider-dots i{display:block;width:8px;height:8px;border-radius:50%;background:rgba(255,255,255,.5)}
.slider-dots i:first-child{background:var(--white)}

/* about / why */
.split-title{width:380px;text-align:right;font-size:62px;line-height:70px;color:#3a3f4c}
.split-text{width:480px;font-size:14px;line-height:24px;color:var(--muted)}

/* services */
.services-title{left:0;width:1200px;text-align:center;font-size:66px;color:var(--navy)}
.photo{border-radius:50%;border:6px solid var(--white);box-shadow:0 6px 18px rgba(0,0,0,.12)}
.svc{display:flex;gap:14px;width:260px}
.svc-icon{flex:none;width:44px;height:44px;border-radius:50%;background:var(--navy);display:flex;align-items:center;justify-content:center}
.svc-icon.is-red{background:var(--red)}
.svc h3{font:700 16px/21px "Open Sans",sans-serif;color:var(--navy)}
.svc p{font-size:11px;line-height:17px;color:var(--muted);margin-top:8px}

/* contact */
.touch-title{left:0;width:1200px;text-align:center;font-size:58px;color:var(--white)}
.foot-brand{left:140px;top:2870px;display:flex;align-items:center;gap:14px;font:700 34px "Roboto",sans-serif;color:var(--white);text-transform:uppercase;width:360px;line-height:40px}
.foot-brand .brand-mark{width:48px;height:48px;flex:none}
.col-title{font:700 13px "Open Sans",sans-serif;color:var(--white);text-transform:uppercase;letter-spacing:.5px}
.contact-list{list-style:none;margin-top:22px;font-size:13px;line-height:20px;color:#c5c9d6}
.contact-list li{display:flex;gap:12px;margin-bottom:16px}
.contact-list svg{flex:none;margin-top:3px}
.links{list-style:none;margin-top:22px;font-size:13px;line-height:21px;color:#c5c9d6}
.form-field{left:690px;width:370px;height:46px;background:var(--white);border-radius:2px;font-size:12px;color:#8a8f9c;padding:14px 14px}
.footer-bar{left:0;top:3460px;width:1200px;height:96px;background:var(--red)}
.socials{left:140px;top:3500px;display:flex;gap:12px}
.socials i{display:block;width:32px;height:32px;border-radius:50%;border:2px solid var(--white)}
.legal{left:560px;top:3508px;font-size:13px;color:var(--white)}
.to-top{left:1120px;top:3516px;font-size:11px;color:var(--white)}
</style>
</head>
<body>

<header class="site-header">
  <div class="brand"><span class="brand-mark"></span>Crestline Advisory</div>
  <nav class="main-nav"><span>Home</span><span>About Company</span><span>The Team</span><span>What We Do</span><span>Contact Us</span></nav>
  <svg class="search" width="16" height="16" viewBox="0 0 16 16"><circle cx="6.5" cy="6.5" r="5" fill="none" stroke="#e3232f" stroke-width="2"/><line x1="10.5" y1="10.5" x2="15" y2="15" stroke="#e3232f" stroke-width="2"/></svg>
</header>

<section class="hero">
  <svg class="abs" width="1200" height="680" viewBox="0 0 1200 680" role="img" aria-label="Dark blue backdrop of glowing business growth charts">
    <defs>
      <linearGradient id="heroGrad" x1="0" y1="0" x2="1" y2="1">
        <stop offset="0" stop-color="#0d1a3d"/>
        <stop offset=".6" stop-color="#13306a"/>
        <stop offset="1" stop-color="#0a1736"/>
      </linearGradient>
    </defs>
    <path d="M0 0H1200V560L600 640 0 560Z" fill="url(#heroGrad)"/>
  </svg>
  <h1 class="abs heading hero-title">Crestline<br>Advisory</h1>
  <p class="abs hero-sub">We help you scale your business operations<br>to become highly profitable.</p>
  <div class="btn" style="left:145px;top:490px"><svg viewBox="0 0 14 14"><path d="M2 12L12 2M5 2h7v7" stroke="#fff" stroke-width="2" fill="none"/></svg>Get Started</div>
  <div class="abs slider-dots"><i></i><i></i><i></i><i></i></div>
</section>

<svg class="abs" style="left:0;top:600px" width="1200" height="170" viewBox="0 0 1200 170">
  <path d="M0 50L600 120 1200 50V170H0Z" fill="#ffffff"/>
  <circle cx="600" cy="100" r="40" fill="#ffffff" stroke="#e6e8ef" stroke-width="2"/>
  <circle cx="600" cy="100" r="18" fill="#e3232f"/>
</svg>

<section>
  <h2 class="abs heading split-title" style="left:110px;top:820px">About<br><span class="red">Crestline</span><br><span class="red">Advisory</span></h2>
  <p class="abs split-text" style="left:560px;top:828px">We are a specialist operational excellence firm, delivering consulting and advisory services in our core capabilities, across all industries and all business lines to improve performance, efficiency, profitability, automation and scalability for clients across Australia.<br>We're known for our pragmatism, in-depth analysis, strategic insight and lasting long-term client self-sufficiency.</p>
  <div class="btn" style="left:560px;top:1040px"><span class="btn-dot"></span>Read More</div>
</section>

<svg class="abs" style="left:0;top:1140px" width="1200" height="960" viewBox="0 0 1200 960">
  <path d="M0 40Q600 -20 1200 40V900Q600 960 0 900Z" fill="#f2f3f8"/>
</svg>

<section>
  <h2 class="abs heading services-title" style="top:1310px">Our <span class="red">Services</span></h2>
  <svg class="abs" style="left:0;top:1380px" width="1200" height="600" viewBox="0 0 1200 600">
    <path d="M290 150H740" stroke="#e3232f" stroke-width="2" fill="none"/>
    <path d="M720 530H930" stroke="#e3232f" stroke-width="2" fill="none"/>
    <path d="M180 280V420H500" stroke="#121a33" stroke-width="2" fill="none"/>
    <circle cx="290" cy="150" r="5" fill="#e3232f"/><circle cx="740" cy="150" r="5" fill="#e3232f"/>
    <circle cx="930" cy="530" r="14" fill="#121a33"/>
  </svg>
  <div class="abs photo" role="img" aria-label="Photo of hands typing on a laptop" style="left:80px;top:1460px;width:200px;height:200px;background:radial-gradient(circle at 40% 40%,#f2c4c0,#c77b79 60%,#8c4a4c)"></div>
  <div class="abs photo" role="img" aria-label="Photo of financial charts on a laptop screen" style="left:745px;top:1380px;width:230px;height:230px;background:radial-gradient(circle at 50% 40%,#eef1f6,#b8c3d6 60%,#6d7f9e)"></div>
  <div class="abs photo" role="img" aria-label="Photo of a calculator and papers on a desk" style="left:490px;top:1730px;width:220px;height:220px;background:radial-gradient(circle at 50% 50%,#e6e6ea,#a8adba 60%,#5d6475)"></div>

  <div class="abs svc" style="left:470px;top:1548px">
    <div class="svc-icon is-red"><svg width="20" height="20" viewBox="0 0 20 20"><path d="M3 16V10M8 16V6M13 16V9M18 16V3" stroke="#fff" stroke-width="2.4"/></svg></div>
    <div><h3>Strategy Analytics &amp;<br>Business Process<br>Optimization</h3><p>We map your processes and find clear gains in cost, speed and control.</p></div>
  </div>
  <div class="abs svc" style="left:110px;top:1830px">
    <div class="svc-icon"><svg width="20" height="20" viewBox="0 0 20 20"><rect x="2" y="4" width="16" height="10" fill="none" stroke="#fff" stroke-width="2"/><path d="M6 17h8" stroke="#fff" stroke-width="2"/></svg></div>
    <div><h3>Market-entry</h3><p>Plans to enter new markets with sound research, pricing and launch steps.</p></div>
  </div>
  <div class="abs svc" style="left:730px;top:1790px">
    <div class="svc-icon"><svg width="20" height="20" viewBox="0 0 20 20"><rect x="4" y="2" width="12" height="16" fill="none" stroke="#fff" stroke-width="2"/><path d="M7 6h6M7 10h6M7 14h3" stroke="#fff" stroke-width="2"/></svg></div>
    <div><h3>Finance, Accounting<br>&amp; Insurance Services</h3><p>Clear books, sound reporting and cover that fits the size of your firm.</p></div>
  </div>
</section>

<section>
  <h2 class="abs heading split-title" style="left:110px;top:2200px">Why We<br><span class="red">Exist</span></h2>
  <p class="abs split-text" style="left:560px;top:2208px">The aim at Crestline Advisory is to be a leading strategy and financial advisory firm across the continent solving complex management problems for small and medium sized enterprises across a wide range of industries. We help you scale your business operations to become highly profitable. We offer your organization cutting-edge expertise leveraging on first-class, strategic and financial insights that help you.</p>
  <div class="btn" style="left:560px;top:2428px"><span class="btn-dot"></span>Read More</div>
</section>

<svg class="abs" style="left:0;top:2560px" width="1200" height="920" viewBox="0 0 1200 920">
  <path d="M0 60L900 90 1200 0V920H0Z" fill="#e3232f"/>
  <path d="M0 80L900 108 1200 24V920H0Z" fill="#121a33"/>
</svg>

<section>
  <h2 class="abs heading touch-title" style="top:2712px">Get In <span class="red">Touch</span></h2>
  <div class="abs foot-brand"><span class="brand-mark"></span><span>Crestline<br>Advisory</span></div>

  <div class="abs" style="left:140px;top:3050px;width:300px">
    <div class="col-title">Contact Details</div>
    <ul class="contact-list">
      <li><svg width="12" height="14" viewBox="0 0 12 14"><path d="M6 13S1 7.5 1 5a5 5 0 0110 0c0 2.5-5 8-5 8z" fill="#e3232f"/></svg>123 Harbour Road, Suite 4<br>Northgate Business Park</li>
      <li><svg width="12" height="12" viewBox="0 0 12 12"><path d="M2 1h3l1 3-2 1a7 7 0 003 3l1-2 3 1v3a1 1 0 01-1 1A10 10 0 011 2a1 1 0 011-1z" fill="#e3232f"/></svg>Phone : +1 555 010 0199</li>
      <li><svg width="13" height="10" viewBox="0 0 13 10"><rect x="0.5" y="0.5" width="12" height="9" fill="none" stroke="#e3232f"/><path d="M1 1l5.5 5L12 1" stroke="#e3232f" fill="none"/></svg>Email : info@crestlineadvisory.example</li>
    </ul>
  </div>
  <div class="abs" style="left:480px;top:3050px">
    <div class="col-title">Quick Links</div>
    <ul class="links"><li>Home</li><li>About company</li><li>The team</li><li>What we do</li><li>Contact us</li></ul>
  </div>

  <div class="abs form-field" style="top:2890px">Enter Name</div>
  <div class="abs form-field" style="top:2950px">Enter Email</div>
  <div class="abs form-field" style="top:3010px">Phone</div>
  <div class="abs form-field" style="top:3070px;height:110px">Message</div>
  <div class="btn" style="left:690px;top:3208px"><span class="btn-dot"></span>Submit Message</div>
</section>

<footer>
  <div class="abs footer-bar"></div>
  <div class="abs socials"><i></i><i></i><i></i><i></i><i></i><i></i></div>
  <div class="abs legal">© 2020 Crestline Advisory All Rights Reserved &nbsp;|&nbsp; Privacy Policy &nbsp;|&nbsp; Terms and Use</div>
  <div class="abs to-top">UP</div>
</footer>

</body>
</html>
```